Graduates Society Sponsorship Brochure

The University of Glenmarrow Graduates Society of New York is putting together a brochure to solicit corporate sponsors for our 5th annual black tie gala in downtown Manhattan.
The Graduates Society works to benefit both the alumni community and to give back to the University. Our Thistle Soirée seeks to bring together former students, friends, and family of Glenmarrow to remind them of their own Thistle Soirée experience during university. We are also promoting Scottish-American relations, and want to make clear to sponsors the benefit of access to our demographic.

Target Market(s)

Corporations, Special Interest Groups, parties with affiliation to Scotland and the UK.

Industry/Entity Type

Non-Profit

Font styles to use
Serif

Colors
ec1f27
0255a3

Requirements
Must have
• Clear details about the separation of sponsorship price points, emphasis on the potential impact and benefit of partnership.
Nice to have
• Some big pictures and lots of icons to show the different sponsorship levels.

```html
<!DOCTYPE html>
<html lang="en">
<head>
<meta charset="utf-8">
<title>Thistle Soirée Sponsorship Brochure – Cover</title>
<link rel="stylesheet" href="https://fonts.googleapis.com/css2?family=Cormorant+Garamond:wght@600;700&display=swap">
<style>
  :root {
    --backdrop: #ececec;
    --page-white: #ffffff;
    --page-grey: #dcdde0;
    --ink-black: #111111;
    --panel-black: #1a1a1a;
    --gold: #e2bd5c;
    --gold-light: #f4dc8c;
    --gold-deep: #9a6a22;
  }
  html, body {
    margin: 0;
    padding: 0;
    width: 1200px;
    height: 1000px;
    overflow: hidden;
    background: var(--backdrop);
    font-family: "Cormorant Garamond", Georgia, serif;
  }
  .spread {
    position: absolute;
    left: 139px;
    top: 174px;
    width: 922px;
    height: 651px;
  }
  .spread-art {
    position: absolute;
    inset: 0;
  }
  .gold-text {
    color: var(--gold);
    font-weight: 700;
    text-align: center;
    position: absolute;
    margin: 0;
    line-height: 1.1;
  }
  .back-cover-address {
    left: 0;
    width: 461px;
    top: 303px;
    font-size: 30px;
    line-height: 40px;
  }
  .front-cover { left: 461px; width: 461px; }
  .event-title {
    top: 52px;
    font-size: 50px;
    line-height: 64px;
    letter-spacing: 0.5px;
  }
  .event-title sup { font-size: 26px; vertical-align: 18px; }
  .event-mark {
    top: 262px;
    display: flex;
    flex-direction: column;
    align-items: center;
    gap: 6px;
  }
  .event-mark-dot {
    width: 34px;
    height: 34px;
    border-radius: 50%;
    background: var(--gold);
  }
  .event-mark-name { font-size: 34px; line-height: 38px; letter-spacing: 1px; }
  .event-mark-year { font-size: 22px; line-height: 24px; }
  .organiser {
    top: 484px;
    font-size: 17px;
    line-height: 22px;
    font-weight: 600;
  }
  .divider {
    position: absolute;
    top: 542px;
    left: 580px;
    width: 222px;
    height: 1px;
    background: var(--gold);
  }
  .divider::after {
    content: "";
    position: absolute;
    left: 107px;
    top: -4px;
    width: 8px;
    height: 8px;
    background: var(--gold);
    transform: rotate(45deg);
  }
  .document-title {
    top: 556px;
    font-size: 34px;
    line-height: 42px;
  }
</style>
</head>
<body>
  <div class="spread">
    <svg class="spread-art" width="922" height="651" viewBox="0 0 922 651" aria-hidden="true">
      <defs>
        <linearGradient id="whitePage" x1="0" y1="0" x2="0" y2="1">
          <stop offset="0" stop-color="var(--page-white)"/>
          <stop offset="1" stop-color="var(--page-grey)"/>
        </linearGradient>
        <linearGradient id="goldBand" x1="0" y1="0" x2="1" y2="0">
          <stop offset="0" stop-color="#8a5a1c"/>
          <stop offset="0.35" stop-color="#f1d27c"/>
          <stop offset="0.6" stop-color="#c9963c"/>
          <stop offset="1" stop-color="#7a4e18"/>
        </linearGradient>
        <radialGradient id="blackPage" cx="0.5" cy="0.35" r="0.8">
          <stop offset="0" stop-color="#2a2a2a"/>
          <stop offset="1" stop-color="#0b0b0b"/>
        </radialGradient>
      </defs>

      <!-- back cover -->
      <rect class="page-back" x="0" y="0" width="461" height="651" fill="url(#whitePage)"/>
      <path d="M0,168 Q230,238 461,168 L461,184 Q230,254 0,184 Z" fill="url(#goldBand)"/>
      <path d="M0,182 Q230,252 461,182 L461,506 Q230,416 0,506 Z" fill="var(--panel-black)"/>
      <path d="M0,504 Q230,414 461,504 L461,520 Q230,430 0,520 Z" fill="url(#goldBand)"/>
      <path d="M21,211 Q231,280 441,211 L441,474 Q231,400 21,474 Z" fill="none" stroke="var(--gold)" stroke-width="1.5"/>

      <!-- front cover -->
      <rect class="page-front" x="461" y="0" width="461" height="651" fill="url(#blackPage)"/>
      <path d="M461,176 Q691,262 922,176 L922,488 Q691,392 461,488 Z" fill="var(--panel-black)"/>
      <path d="M461,150 Q691,236 922,150 L922,178 Q691,262 461,178 Z" fill="url(#goldBand)"/>
      <path d="M461,484 Q691,388 922,484 L922,504 Q691,408 461,504 Z" fill="url(#goldBand)"/>
      <path d="M483,214 Q692,282 901,214 L901,474 Q692,398 483,474 Z" fill="none" stroke="var(--gold)" stroke-width="1.5"/>
    </svg>

    <p class="gold-text back-cover-address">Suite 2406<br>New York, NY.</p>

    <h1 class="gold-text front-cover event-title">5<sup>th</sup>Annual<br>Thistle Soirée</h1>

    <div class="gold-text front-cover event-mark">
      <span class="event-mark-dot"></span>
      <span class="event-mark-name">THISTLE SOIRÉE</span>
      <span class="event-mark-year">2018</span>
    </div>

    <p class="gold-text front-cover organiser">University of Glenmarrow<br>Graduates Society of New York</p>
    <div class="divider"></div>
    <h2 class="gold-text front-cover document-title">Sponsorship<br>Brochure</h2>
  </div>
</body>
</html>
```